Wordpress website for a new Podcast

Hi, We are looking for a designer to create a wordpress website project for a new podcast and publish it on the domain we own.

The show is called “Bright Gatherings” (logo included) and its aim is to interview guests who work as professional facilitators, trainers, teachers and coaches. The show has a positive vibe, is fun, vibrant and full of positive energy. These are the feelings we want to convey in the design.

The website should have a similar structure to: https://www.plumvesselcast.example/ with the following content:

1) The main page including:
- navigation bar and social buttons at the top
- main graphic design featuring the latest episode
- "latest episodes" section displaying 3 episodes (please design a mask to be used for new episodes when they air together with the face of the interviewee) -> this will link to the respective episodes
- please design an "bright gatherings" book cover mockup to be inluded as a banner -> this will link to Orindel
- subscribe to the newsletter - a banner capturing the name and email of the user -> to be connected to PostWren.
-> a working episode search.

2) Episodes page
- the show will be divided into seasons (12 episodes each) and each episode will need a separate "blog entry" including:
-> A short article (4-5 paragraphs) + stock image
-> interviewee's bio and social links

3) Meet the hosts page
- including bios of the two hosts of the show
- links to their social profiles
- a "request speaker availability" form which sends an email

Some additional nice-to-haves:
1) Good and clean Bio's would be awesome (both for the hosts & the interviewees),
2) an easily navigable episode system,
3) a keyword/date search option
4) easy to share options (share to WhatsApp, Facebook, Twitter, LinkedIn) 5) We must be able to track how the podcasts are shared (google analytics?)

```html
<!DOCTYPE html>
<html lang="en">
<head>
<meta charset="utf-8">
<title>Bright Gatherings — Podcast</title>
<link href="https://fonts.googleapis.com/css2?family=Josefin+Sans:wght@600;700&family=Roboto:wght@400;500;700&display=swap" rel="stylesheet">
<style>
:root{
  --orange:#f0461b;
  --orange-deep:#d8330f;
  --amber:#f5a21c;
  --dark:#232323;
  --darker:#1b1b1b;
  --ink:#1e1e1e;
  --text:#6b6b6b;
  --muted:#9a9a9a;
  --line:#e4e4e4;
  --white:#fff;
}
*{box-sizing:border-box;margin:0;padding:0}
html,body{width:1200px;height:4751px;overflow:hidden}
body{position:relative;background:var(--white);font-family:'Roboto',sans-serif;color:var(--text)}
.abs{position:absolute}
.display{font-family:'Josefin Sans',sans-serif;font-weight:700;text-transform:uppercase;letter-spacing:1px}
.accent{color:var(--orange)}
.btn{position:absolute;display:flex;align-items:center;justify-content:center;gap:6px;font:700 14px 'Roboto',sans-serif;text-transform:uppercase;color:var(--white);background:var(--orange);text-decoration:none}
.btn .arrow{width:13px;height:13px;border-radius:50%;background:currentColor;position:relative}
.btn .arrow::after{content:"";position:absolute;left:4px;top:3.5px;border-left:5px solid var(--orange);border-top:3px solid transparent;border-bottom:3px solid transparent}
.btn.ghost{background:var(--white);color:var(--orange)}
.btn.ghost .arrow::after{border-left-color:var(--white)}

/* header */
.site-header{position:absolute;left:0;top:0;width:1200px;height:100px;background:var(--orange)}
.nav{position:absolute;left:144px;top:40px;display:flex;gap:32px;font:500 15px 'Roboto',sans-serif;color:var(--white)}
.brand-disc{position:absolute;left:498px;top:-34px;width:204px;height:204px;border-radius:50%;background:radial-gradient(circle at 50% 40%,var(--amber),var(--orange) 70%)}
.brand-name{position:absolute;left:498px;top:34px;width:204px;text-align:center;font:700 25px/1.05 'Josefin Sans',sans-serif;color:var(--white);text-transform:uppercase}
.social{position:absolute;display:flex;gap:14px}
.social span{width:14px;height:14px;border-radius:50%;background:var(--white)}
.btn-book{left:888px;top:30px;width:168px;height:40px;background:#111;font-size:13px}

/* hero */
.hero{position:absolute;left:0;top:100px;width:1200px;height:552px;background:linear-gradient(135deg,#2b2b2b,#1f1f1f)}
.hero h1{position:absolute;left:146px;top:212px;font-size:41px;color:var(--white)}
.hero p{position:absolute;left:146px;top:276px;width:420px;font:500 17px/25px 'Roboto',sans-serif;color:var(--white)}
.book-base{position:absolute;left:697px;top:617px;width:503px;height:66px;border-radius:50%;background:var(--amber)}
.book{position:absolute;overflow:hidden}
.book .spine{position:absolute;left:0;top:0;width:14px;height:100%;background:linear-gradient(90deg,rgba(0,0,0,.35),rgba(0,0,0,0))}
.book .title{position:absolute;left:0;width:100%;text-align:center;font-family:'Josefin Sans',sans-serif;font-weight:700;text-transform:uppercase;line-height:1.05}
.book .author{position:absolute;font:500 17px/1.4 'Roboto',sans-serif;text-align:right}
.book .clouds{position:absolute;left:0;bottom:0;width:100%}

/* section headings */
.sec-title{position:absolute;left:0;width:1200px;text-align:center}
.sec-title .ghost-word{position:absolute;left:0;width:1200px;top:-28px;font-size:80px;color:#ececec;letter-spacing:3px}
.sec-title h2{position:relative;font-size:44px;color:var(--ink)}
.lead{position:absolute;left:0;width:1200px;text-align:center;font-size:14px;line-height:25px;color:var(--text)}
.lead span{display:block}

/* episode cards */
.ep-card{position:absolute;top:907px;width:288px;height:438px;background:var(--white);border:1px solid var(--line);box-shadow:0 2px 10px rgba(0,0,0,.06)}
.ep-card .media{height:188px}
.ep-card h3{margin:30px 0 0 20px;font:500 22px 'Roboto',sans-serif;color:var(--ink)}
.ep-card .ep-no{margin:6px 0 0 20px;font:500 14px 'Roboto',sans-serif;color:var(--orange)}
.ep-card p{margin:18px 20px 0;font-size:14px;line-height:26px;text-align:justify;color:var(--muted)}
.ep-card .btn{left:20px;top:379px;width:122px;height:36px;font-size:13px}

/* hosts */
.hosts-band{position:absolute;left:0;top:2010px}
.vertical{position:absolute;font-family:'Josefin Sans',sans-serif;font-weight:700;font-size:80px;letter-spacing:4px;text-transform:uppercase;transform:rotate(-90deg);transform-origin:left top;white-space:nowrap}

/* articles */
.art-card{position:absolute;width:437px;height:194px;background:var(--white);box-shadow:0 2px 10px rgba(0,0,0,.08)}
.art-card .media{position:absolute;left:0;top:0;width:173px;height:194px}
.art-card h4{position:absolute;left:197px;top:22px;font:500 15px 'Roboto',sans-serif;color:var(--ink);text-transform:uppercase}
.art-card .date{position:absolute;left:197px;top:50px;font-size:12px;color:var(--ink);display:flex;gap:6px;align-items:center}
.art-card .date i{width:10px;height:10px;background:var(--orange);display:block}
.art-card p{position:absolute;left:197px;top:78px;width:220px;font-size:11px;line-height:21px;color:var(--muted)}
.art-card .more{position:absolute;left:197px;top:164px;font:500 12px 'Roboto',sans-serif;color:var(--orange);text-decoration:underline;text-transform:uppercase}
.art-card .count{position:absolute;right:24px;top:164px;font-size:11px;color:var(--muted)}

/* publications */
.pub{position:absolute;top:4230px;width:167px;height:83px;border:1px solid var(--line);display:flex;align-items:center;justify-content:center;font:600 21px 'Josefin Sans',sans-serif;color:#333;background:var(--white)}

/* footer */
.site-footer{position:absolute;left:0;top:4360px;width:1200px;height:391px;background:var(--darker);color:var(--white)}
.f-col{position:absolute;top:84px}
.f-col h5{font:700 16px 'Roboto',sans-serif;text-transform:uppercase;letter-spacing:.3px}
.f-col ul{list-style:none;margin-top:22px;font-size:13px;line-height:27px}
.f-col ul li::before{content:"»";margin-right:14px}
.f-contact{margin-top:22px;font-size:13px;line-height:21px}
.f-contact div{position:relative;padding-left:26px;margin-bottom:22px}
.f-contact i{position:absolute;left:0;top:4px;width:10px;height:10px;background:var(--white);border-radius:50%}
</style>
</head>
<body>

<!-- header -->
<header class="site-header">
  <nav class="nav"><span>HOME</span><span>EPISODES</span><span>MEET THE HOSTS</span></nav>
  <div class="brand-disc"></div>
  <div class="brand-name">Bright<br>Gatherings</div>
  <div class="social" style="left:744px;top:43px" aria-label="Social links">
    <span></span><span></span><span></span><span></span><span></span>
  </div>
  <a class="btn btn-book">Get the book now</a>
</header>

<!-- hero -->
<section class="hero">
  <h1 class="display">Bright Gatherings</h1>
  <p>Lorem ipsum dolor sit amet, consectetur adipiscing sed eiusmod tempor incididunt.</p>
  <a class="btn" style="left:146px;top:349px;width:202px;height:43px">Get the book now <i class="arrow"></i></a>
  <a class="btn ghost" style="left:358px;top:349px;width:202px;height:43px">Get free trained <i class="arrow"></i></a>
</section>
<div class="book-base"></div>
<div class="book" style="left:794px;top:276px;width:312px;height:373px;background:#ececec;box-shadow:0 6px 20px rgba(0,0,0,.3)">
  <div class="title" style="top:34px;font-size:44px;color:var(--ink)"><span class="accent" style="font-size:28px">Bright</span><br>Gatherings</div>
  <div class="book-art clouds" role="img" aria-label="Orange cloud illustration along the cover base" style="height:120px;background:linear-gradient(180deg,rgba(240,70,27,0),var(--orange) 55%,var(--orange-deep))"></div>
  <div class="author" style="right:22px;top:254px;color:var(--ink)">Auther Name Here<br><span style="font-size:15px">- Jhon</span></div>
  <div class="spine"></div>
</div>

<!-- latest episodes -->
<div class="sec-title display" style="top:730px"><div class="ghost-word">Latest Episodes</div><h2>Latest <span class="accent">Episodes</span></h2></div>
<p class="lead" style="top:818px"><span>Lorem ipsum dolor sit amet, consectetur adipiscing elit, sed do eiusmod tempor incididunt ut labore et dolore</span><span>magna aliqua. Quis ipsum suspendisse ultrices gravida. Risus commodo viverra.</span></p>

<article class="ep-card" style="left:138px">
  <div class="media" role="img" aria-label="Microphone on stage at a conference" style="background:linear-gradient(135deg,#3a2a20,#6a5a4c 55%,#1e1a16)"></div>
  <h3>Latest Episode Name</h3><div class="ep-no">Episode 100</div>
  <p>Dignissimos et ducimus atque qui blanditiis praesentium voluptatum deleniti et quas.</p>
  <a class="btn">Explore <i class="arrow"></i></a>
</article>
<article class="ep-card" style="left:457px">
  <div class="media" role="img" aria-label="Business handshake in a bright office" style="background:linear-gradient(135deg,#dfe6ee,#b8c4d2 60%,#eef2f6)"></div>
  <h3>Latest Episode Name</h3><div class="ep-no">Episode 101</div>
  <p>Dignissimos et ducimus atque qui blanditiis praesentium voluptatum deleniti et quas.</p>
  <a class="btn">Explore <i class="arrow"></i></a>
</article>
<article class="ep-card" style="left:776px">
  <div class="media" role="img" aria-label="Guest on a phone call at an office desk" style="background:linear-gradient(135deg,#c9ccd0,#8e8a86 60%,#d6d3cf)"></div>
  <h3>Latest Episode Name</h3><div class="ep-no">Episode 102</div>
  <p>Dignissimos et ducimus atque qui blanditiis praesentium voluptatum deleniti et quas.</p>
  <a class="btn">Explore <i class="arrow"></i></a>
</article>

<div class="abs" style="left:144px;top:1455px;width:912px;height:1px;background:var(--line)"></div>

<!-- about -->
<div class="sec-title display" style="top:1532px"><div class="ghost-word">Bright Gatherings</div><h2>About Bright <span class="accent">Gatherings</span></h2></div>
<p class="lead" style="top:1619px"><span>Lorem ipsum dolor sit amet, consectetur adipiscing elit, sed do eiusmod tempor incididunt ut labore et dolore magna</span><span>aliqua. Quis ipsum suspendisse ultrices gravida. Risus commodo viverra.</span></p>
<p class="lead" style="top:1693px"><span>Lorem ipsum dolor sit amet, consectetur adipiscing elit, sed do eiusmod tempor incididunt ut labore et dolore magna</span><span>aliqua. Ut enim ad minim veniam, quis nostrud exercitation ullamco laboris nisi ut aliquip ex ea commodo consequat.</span><span>Duis aute irure dolor in reprehenderit in voluptate velit esse cillum dolore eu fugiat nulla pariatur.</span></p>

<!-- hosts band -->
<svg class="hosts-band" width="1200" height="552" viewBox="0 0 1200 552" aria-hidden="true"><polygon points="0,18 1200,70 1200,552 0,552" fill="#222"/></svg>
<div class="vertical" style="left:12px;top:2530px;color:#3a3a3a">The Hosts</div>

<div class="abs" role="img" aria-label="Interview being filmed with a camera in a studio" style="left:315px;top:1806px;width:570px;height:326px;background:linear-gradient(120deg,#4b4f55,#a9a39a 45%,#2f3237)"></div>
<svg class="abs" style="left:572px;top:1951px" width="56" height="38" viewBox="0 0 56 38" aria-label="Play video"><rect width="56" height="38" rx="10" fill="#e62117"/><polygon points="22,11 36,19 22,27" fill="#fff"/></svg>

<h2 class="abs display" style="left:142px;top:2222px;font-size:44px;color:var(--white)">Meet the Hosts</h2>
<p class="abs" style="left:144px;top:2289px;width:436px;font-size:14px;line-height:28px;color:var(--white);text-align:justify">Lorem ipsum dolor sit amet, consectetur adipiscing elit, sed do eiusmod tempor incididunt ut labore et dolore magna aliqua. Quis ipsum suspendisse ultrices gravida. Risus commodo viverra maecenas accumsan lacus vel facilisis.</p>
<a class="btn" style="left:144px;top:2427px;width:164px;height:44px;font-size:15px">Meet now <i class="arrow"></i></a>
<div class="abs" role="img" aria-label="Portrait of the show host in a grey suit" style="left:793px;top:2129px;width:331px;height:433px;background:linear-gradient(180deg,#3b3d44,#52555e 50%,#2a2b30)"></div>

<!-- articles -->
<div class="sec-title display" style="top:2668px"><div class="ghost-word">Latest Articles</div><h2>Latest <span class="accent">Articles</span></h2></div>
<p class="lead" style="top:2734px"><span>Lorem ipsum dolor sit amet, consectetur adipiscing elit, sed do eiusmod tempor incididunt</span><span>sit amet, ut labore et dolore magna aliqua.</span></p>

<article class="art-card" style="left:144px;top:2814px">
  <div class="media" role="img" aria-label="Hand holding a microphone out to a speaker" style="background:linear-gradient(135deg,#4f6a7e,#9aaebc 55%,#2c3a45)"></div>
  <h4>Ipsam voluptatem</h4><div class="date"><i></i>JUN 09, 2019</div>
  <p>At vero eos et accusam muset iusto odio dignissimos ducimus qu praeseum tre voluptatum deleniti atque</p>
  <a class="more">Read more</a><span class="count">35 comments</span>
</article>
<article class="art-card" style="left:617px;top:2814px">
  <div class="media" role="img" aria-label="Guest seated at a desk in a dark office" style="background:linear-gradient(135deg,#2c2a28,#6d5b4e 55%,#1e1c1a)"></div>
  <h4>Accusamus et iusto</h4><div class="date"><i></i>JUN 09, 2019</div>
  <p>At vero eos et accusam muset iusto odio dignissimos ducimus qu praeseum tre voluptatum deleniti atque</p>
  <a class="more">Read more</a><span class="count">35 comments</span>
</article>
<article class="art-card" style="left:144px;top:3041px">
  <div class="media" role="img" aria-label="Speaker presenting in a suit" style="background:linear-gradient(135deg,#b9c2c8,#5d6670 55%,#2d3238)"></div>
  <h4>Ipsam voluptatem</h4><div class="date"><i></i>JUN 09, 2019</div>
  <p>At vero eos et accusam muset iusto odio dignissimos ducimus qu praeseum tre voluptatum deleniti atque</p>
  <a class="more">Read more</a><span class="count">35 comments</span>
</article>
<article class="art-card" style="left:617px;top:3041px">
  <div class="media" role="img" aria-label="Guest reading at a table surrounded by plants" style="background:linear-gradient(135deg,#2f4a2a,#6f8a5a 55%,#c9c2b0)"></div>
  <h4>Accusamus et iusto</h4><div class="date"><i></i>JUN 09, 2019</div>
  <p>At vero eos et accusam muset iusto odio dignissimos ducimus qu praeseum tre voluptatum deleniti atque</p>
  <a class="more">Read more</a><span class="count">35 comments</span>
</article>
<a class="btn" style="left:498px;top:3280px;width:204px;height:38px;font-size:13px">View all articles <i class="arrow"></i></a>

<!-- book band -->
<section class="abs" style="left:0;top:3428px;width:1200px;height:470px;background:var(--dark)"></section>
<div class="vertical" style="left:4px;top:3880px;color:#3c3c3c">Our Book</div>
<div class="book" style="left:155px;top:3529px;width:381px;height:461px;background:#2d2d2d;box-shadow:0 8px 24px rgba(0,0,0,.4)">
  <div class="title" style="top:52px;font-size:54px;color:var(--orange)"><span style="color:var(--white);font-size:36px">Bright</span><br>Gatherings</div>
  <div class="book-art clouds" role="img" aria-label="Orange cloud illustration along the cover base" style="height:150px;background:linear-gradient(180deg,rgba(240,70,27,0),var(--orange) 50%,var(--orange-deep))"></div>
  <div class="author" style="right:35px;top:290px;color:var(--white);font-size:20px">Auther Name Here<br>- Jhon</div>
  <div class="spine"></div>
</div>
<h2 class="abs display" style="left:625px;top:3524px;font-size:39px;line-height:48px;color:var(--white)">Bright Gatherings<br>Book</h2>
<p class="abs" style="left:625px;top:3640px;width:440px;font-size:14px;line-height:28px;color:var(--white)">I must explain to you how all this mistaken idea denouncing pleasure praising pain was born and I will give you a complete.</p>
<form class="abs" style="left:625px;top:3725px;width:424px;height:42px;border:1px solid #888;display:flex;align-items:center;padding:3px">
  <span style="flex:1;padding-left:20px;font-size:13px;color:var(--white)">Email Address</span>
  <span class="btn" style="position:static;width:122px;height:34px;font-size:13px">Download</span>
</form>

<!-- publications -->
<div class="sec-title display" style="top:4078px"><div class="ghost-word">Our Publications</div><h2>Our <span class="accent">Publications</span></h2></div>
<p class="lead" style="top:4148px"><span>Lorem ipsum dolor sit amet, consectetur adipiscing elit, sed do eiusmod tempor incididunt ut labore et dolore</span><span>magna aliqua. Ut enim ad minim veniam, quis nostrud exercitation ullamco laboris.</span></p>
<div class="pub" style="left:144px">Frost Parlour</div>
<div class="pub" style="left:331px">Nimbo Events</div>
<div class="pub" style="left:517px">Swirlo</div>
<div class="pub" style="left:703px">Velmora</div>
<div class="pub" style="left:889px">Visit Harwick</div>

<!-- footer -->
<footer class="site-footer">
  <div class="abs" style="left:144px;top:82px;width:200px;font:700 29px/1.05 'Josefin Sans',sans-serif;color:var(--orange);text-transform:uppercase">Bright<br>Gatherings</div>
  <div class="f-col" style="left:385px"><h5>Quick Links</h5>
    <ul><li>Home</li><li>Episodes</li><li>Meet The Hosts</li><li>Privacy Policy</li><li>Terms Of Services</li></ul></div>
  <div class="f-col" style="left:577px"><h5>Contact Us</h5>
    <div class="f-contact"><div><i></i>123 New Street, Sample City,<br>Old State, USA</div><div><i></i>(+1) 123 456 7890</div><div><i></i>info@brightgatherings.example</div></div></div>
  <div class="f-col" style="left:816px;width:240px"><h5>Newsletter Subscription</h5>
    <p style="margin-top:20px;font-size:12px;line-height:20px">Register your Email Address to get more Information about us</p>
    <div style="margin-top:10px;width:238px;height:32px;border:1px solid #777;font-size:11px;padding:9px 12px">Email Address</div>
    <div class="btn" style="position:relative;margin-top:12px;width:100px;height:32px;font-size:11px">Subscribe</div></div>
  <div class="abs" style="left:144px;top:299px;width:360px;height:1px;background:#555"></div>
  <div class="abs" style="left:696px;top:299px;width:360px;height:1px;background:#555"></div>
  <div class="abs" style="left:518px;top:284px;display:flex;gap:12px" aria-label="Social links">
    <span style="width:32px;height:32px;border:2px solid #fff;border-radius:50%"></span><span style="width:32px;height:32px;border:2px solid #fff;border-radius:50%"></span><span style="width:32px;height:32px;border:2px solid #fff;border-radius:50%"></span><span style="width:32px;height:32px;border:2px solid #fff;border-radius:50%"></span>
  </div>
  <p class="abs" style="left:0;top:340px;width:1200px;text-align:center;font-size:14px">Copyrights © 2019 Bright Gatherings. All Rights Reserved &nbsp;&nbsp;|&nbsp;&nbsp; Site Map</p>
</footer>

</body>
</html>
```